we need a business card. We are an online company that provides work life balance services to our members. our website can be viewed at www.corvinta3go.com.au
Our company logo is attached as well as a business card look that i like.

```html
<!DOCTYPE html>
<html lang="en">
<head>
<meta charset="utf-8">
<title>corvinta3go business card</title>
<link rel="stylesheet" href="https://fonts.googleapis.com/css2?family=Jura:wght@500;700&display=swap">
<style>
  :root {
    --backdrop: #e7e4df;
    --card: #f7f7f6;
    --green-dark: #2f8f3e;
    --green-mid: #3fa34d;
    --green-light: #7cc242;
    --ink: #2b2b2b;
    --muted: #444;
  }
  html, body {
    margin: 0;
    padding: 0;
    width: 1200px;
    height: 958px;
    overflow: hidden;
    background: var(--backdrop);
  }
  .card {
    position: absolute;
    left: 100px;
    top: 193px;
    width: 1000px;
    height: 572px;
    background: var(--card);
    box-shadow: 0 14px 40px rgba(0,0,0,0.18);
    font-family: "Jura", sans-serif;
    color: var(--ink);
    overflow: hidden;
  }
  .card__band {
    position: absolute;
    left: 0;
    top: 0;
  }
  .brand {
    position: absolute;
    left: 110px;
    top: 62px;
    display: flex;
    align-items: center;
    gap: 22px;
  }
  .brand__dot {
    width: 74px;
    height: 74px;
    border-radius: 50%;
    background: var(--green-mid);
  }
  .brand__name {
    font-size: 58px;
    font-weight: 500;
    color: var(--green-mid);
    letter-spacing: 0.5px;
  }
  .person {
    position: absolute;
    left: 140px;
    top: 205px;
  }
  .person__name {
    margin: 0;
    font-size: 32px;
    font-weight: 700;
    color: var(--green-mid);
    letter-spacing: 1.5px;
  }
  .person__role {
    margin: 6px 0 0 10px;
    font-size: 21px;
    font-weight: 700;
    color: var(--muted);
  }
  .contact {
    position: absolute;
    list-style: none;
    margin: 0;
    padding: 0;
  }
  .contact--left { left: 150px; top: 320px; }
  .contact--right { left: 560px; top: 222px; }
  .contact__item {
    display: flex;
    align-items: center;
    gap: 22px;
    height: 38px;
    margin-bottom: 20px;
    font-size: 21px;
    font-weight: 700;
    color: var(--muted);
  }
  .contact__icon {
    width: 36px;
    height: 36px;
    background: var(--green-mid);
    border-radius: 3px;
    display: flex;
    align-items: center;
    justify-content: center;
    flex: none;
  }
</style>
</head>
<body>
<div class="card">
  <svg class="card__band" width="90" height="572" viewBox="0 0 90 572">
    <polygon points="0,0 48,0 48,150 0,300" fill="var(--green-dark)"/>
    <polygon points="0,322 86,150 86,572 0,572" fill="var(--green-light)"/>
  </svg>

  <div class="brand">
    <div class="brand__dot"></div>
    <div class="brand__name">corvinta3go</div>
  </div>

  <div class="person">
    <h1 class="person__name">DANIEL WHITFORD</h1>
    <p class="person__role">Managing Director</p>
  </div>

  <ul class="contact contact--left">
    <li class="contact__item">
      <span class="contact__icon">
        <svg width="18" height="20" viewBox="0 0 18 20"><path d="M9 1a6 6 0 0 0-6 6c0 4.5 6 12 6 12s6-7.5 6-12a6 6 0 0 0-6-6z" fill="#fff"/><circle cx="9" cy="7" r="2.2" fill="var(--green-mid)"/></svg>
      </span>
      Harbour Lane, 27
    </li>
    <li class="contact__item">
      <span class="contact__icon">
        <svg width="18" height="18" viewBox="0 0 18 18"><path d="M4 1l3 4-2 2c1 2 3 4 5 5l2-2 4 3-2 3C8 16 2 10 1 4z" fill="#fff"/></svg>
      </span>
      012 555 0148
    </li>
    <li class="contact__item">
      <span class="contact__icon">
        <svg width="20" height="14" viewBox="0 0 20 14"><rect x="1" y="1" width="18" height="12" fill="#fff"/><path d="M1 1l9 7 9-7" fill="none" stroke="var(--green-mid)" stroke-width="1.6"/></svg>
      </span>
      hello@corvinta3go.com.au
    </li>
  </ul>

  <ul class="contact contact--right">
    <li class="contact__item">
      <span class="contact__icon">
        <svg width="20" height="20" viewBox="0 0 20 20" fill="none" stroke="#fff" stroke-width="1.6"><circle cx="10" cy="10" r="8"/><ellipse cx="10" cy="10" rx="3.5" ry="8"/><path d="M2 10h16M3.5 6h13M3.5 14h13"/></svg>
      </span>
      www.corvinta3go.com.au
    </li>
  </ul>
</div>
</body>
</html>
```